Working Capital graphics

Our business advisory firm requires 9 images to be re-created and improved in the branding of our business.

The 9 images have been uploaded below and the colours and branding of the business can be found at the website www.tallowmereadvisory.com.au

```html
<!DOCTYPE html>
<html lang="en">
<head>
<meta charset="utf-8">
<title>Inventories – Inventory Drivers</title>
<link rel="stylesheet" href="https://fonts.googleapis.com/css2?family=Figtree:ital,wght@0,600;1,700;1,800&display=swap">
<style>
  :root {
    --box-blue: #55a8dd;
    --badge-orange: #f29b40;
    --ink: #111111;
    --connector: #111111;
    --paper: #ffffff;
  }
  html, body {
    margin: 0;
    padding: 0;
    width: 1200px;
    height: 1000px;
    overflow: hidden;
    background: var(--paper);
  }
  .driver-tree {
    display: block;
    width: 1200px;
    height: 1000px;
    font-family: "Figtree", "Helvetica Neue", Arial, sans-serif;
  }
  .page-title {
    font-size: 35px;
    font-weight: 800;
    font-style: italic;
    fill: var(--ink);
  }
  .column-heading {
    font-size: 17px;
    font-weight: 600;
    fill: var(--ink);
  }
  .box { fill: var(--box-blue); }
  .root-label {
    font-size: 21px;
    font-weight: 700;
    font-style: italic;
    fill: var(--ink);
  }
  .group-label {
    font-size: 19px;
    font-weight: 700;
    font-style: italic;
    fill: var(--ink);
  }
  .sub-label {
    font-size: 17px;
    font-weight: 700;
    font-style: italic;
    fill: var(--ink);
  }
  .badge { fill: var(--badge-orange); }
  .badge-number {
    font-size: 30px;
    font-weight: 800;
    font-style: italic;
    fill: var(--paper);
    letter-spacing: -2px;
  }
  .connector {
    fill: none;
    stroke: var(--connector);
    stroke-width: 1.6;
  }
</style>
</head>
<body>
<svg class="driver-tree" viewBox="0 0 1200 1000" role="img" aria-label="Inventory drivers tree: Planning, Procurement, Fulfilment and Product Range with their sub-groups">
  <text class="page-title" x="120" y="174">Inventories</text>
  <text class="column-heading" x="566" y="177" text-anchor="middle">Driver Group</text>
  <text class="column-heading" x="913" y="177" text-anchor="middle">Sub-groups</text>

  <!-- connectors -->
  <g class="connectors">
    <path class="connector" d="M325 502 H398 M398 297 V783 M398 297 H440 M398 476 H440 M398 627 H440 M398 783 H440"/>
    <path class="connector" d="M666 296 H697 M697 218 V372 M697 218 H730 M697 269 H730 M697 321 H730 M697 372 H730"/>
    <path class="connector" d="M666 476 H697 M697 425 V528 M697 425 H730 M697 476 H730 M697 528 H730"/>
    <path class="connector" d="M666 627 H697 M697 580 V674 M697 580 H730 M697 627 H730 M697 674 H730"/>
    <path class="connector" d="M666 784 H697 M697 735 V837 M697 735 H730 M697 784 H730 M697 837 H730"/>
  </g>

  <!-- root -->
  <g class="root-node">
    <rect class="box" x="120" y="448" width="205" height="109"/>
    <text class="root-label" x="222" y="498" text-anchor="middle">Inventory</text>
    <text class="root-label" x="222" y="523" text-anchor="middle">Drivers</text>
  </g>

  <!-- driver groups -->
  <g class="driver-group">
    <rect class="box" x="452" y="274" width="214" height="43"/>
    <circle class="badge" cx="453" cy="295" r="27"/>
    <text class="badge-number" x="451" y="306" text-anchor="middle">10</text>
    <text class="group-label" x="564" y="302" text-anchor="middle">Planning</text>
  </g>
  <g class="driver-group">
    <rect class="box" x="452" y="454" width="214" height="43"/>
    <circle class="badge" cx="453" cy="475" r="27"/>
    <text class="badge-number" x="451" y="486" text-anchor="middle">11</text>
    <text class="group-label" x="564" y="482" text-anchor="middle">Procurement</text>
  </g>
  <g class="driver-group">
    <rect class="box" x="452" y="605" width="214" height="43"/>
    <circle class="badge" cx="453" cy="626" r="27"/>
    <text class="badge-number" x="451" y="637" text-anchor="middle">12</text>
    <text class="group-label" x="564" y="633" text-anchor="middle">Fulfilment</text>
  </g>
  <g class="driver-group">
    <rect class="box" x="452" y="762" width="214" height="43"/>
    <circle class="badge" cx="453" cy="783" r="27"/>
    <text class="badge-number" x="451" y="794" text-anchor="middle">13</text>
    <text class="group-label" x="564" y="790" text-anchor="middle">Product Range</text>
  </g>

  <!-- sub-groups -->
  <g class="sub-groups">
    <rect class="box" x="730" y="203" width="336" height="30"/>
    <text class="sub-label" x="898" y="224" text-anchor="middle">Demand variability</text>
    <rect class="box" x="730" y="254" width="336" height="30"/>
    <text class="sub-label" x="898" y="275" text-anchor="middle">Planning collaboration</text>
    <rect class="box" x="730" y="306" width="336" height="30"/>
    <text class="sub-label" x="898" y="327" text-anchor="middle">Information availability</text>
    <rect class="box" x="730" y="357" width="336" height="30"/>
    <text class="sub-label" x="898" y="378" text-anchor="middle">Inventory target setting</text>

    <rect class="box" x="730" y="410" width="336" height="30"/>
    <text class="sub-label" x="898" y="431" text-anchor="middle">Order quantities</text>
    <rect class="box" x="730" y="461" width="336" height="30"/>
    <text class="sub-label" x="898" y="482" text-anchor="middle">Supplier lead time variability</text>
    <rect class="box" x="730" y="513" width="336" height="30"/>
    <text class="sub-label" x="898" y="534" text-anchor="middle">Supplier quality variability</text>

    <rect class="box" x="730" y="565" width="336" height="30"/>
    <text class="sub-label" x="898" y="586" text-anchor="middle">Customer service leads</text>
    <rect class="box" x="730" y="612" width="336" height="30"/>
    <text class="sub-label" x="898" y="633" text-anchor="middle">Network structure</text>
    <rect class="box" x="730" y="659" width="336" height="30"/>
    <text class="sub-label" x="898" y="680" text-anchor="middle">Supplier quality variability</text>

    <rect class="box" x="730" y="720" width="336" height="30"/>
    <text class="sub-label" x="898" y="741" text-anchor="middle">Customer service leads</text>
    <rect class="box" x="730" y="769" width="336" height="30"/>
    <text class="sub-label" x="898" y="790" text-anchor="middle">Parts standardisation</text>
    <rect class="box" x="730" y="822" width="336" height="30"/>
    <text class="sub-label" x="898" y="843" text-anchor="middle">SKU proliferation</text>
  </g>
</svg>
</body>
</html>
```